Boutique custom software development company needs new business card

Our nearly 20 year old custom software development company would like to better include the fact that we are now providing Bitcoin services. These new services are B2B include education (how to acquire and securely hold Bitcoin) and integrating Bitcoin payments into existing ecommerce sites or other existing systems. Please keep the card clean and simple. Attached is our current design and some other files. vextorial.com

Target Market(s)

businesses owners interested in long term relationship

Industry/Entity Type

Custom software development and Bitcoin

Contact Information for Business Card

Dale Parker, dale@vextorial.com, vextorial.com, (888) 555-VXTRL

Font styles to use
Other font styles liked:
• monospace

Requirements
Must have
• double-sided
Nice to have
• clean and simple
Should not have
• physical address

```html
<!DOCTYPE html>
<html lang="en">
<head>
<meta charset="utf-8">
<title>Vextorial business card</title>
<link rel="stylesheet" href="https://fonts.googleapis.com/css2?family=Open+Sans:wght@400;600;700;800&display=swap">
<style>
  :root {
    --orange: #f07e22;
    --blue: #3d76bb;
    --white: #ffffff;
    --ink: #111111;
    --backdrop: #e9e9e9;
  }
  * { box-sizing: border-box; margin: 0; padding: 0; }
  html, body { width: 1200px; height: 936px; overflow: hidden; }
  body {
    background: var(--backdrop);
    font-family: "Open Sans", Arial, sans-serif;
    position: relative;
  }
  .card {
    position: absolute;
    width: 560px;
    height: 320px;
    overflow: hidden;
    box-shadow: 0 6px 18px rgba(0,0,0,0.18);
  }

  /* Front */
  .card-front {
    left: 60px; top: 70px;
    background: var(--orange);
    display: flex; flex-direction: column; justify-content: center; align-items: center;
  }
  .front-brand { display: flex; align-items: center; gap: 14px; }
  .front-brand .brand-square { width: 34px; height: 34px; background: var(--ink); }
  .front-brand .brand-name {
    font-size: 66px; font-weight: 800; color: var(--ink); letter-spacing: -1px; line-height: 1;
  }
  .front-tagline {
    margin-top: 8px; font-size: 27px; font-weight: 400; color: var(--ink); letter-spacing: -0.5px;
  }

  /* Back */
  .card-back {
    left: 580px; top: 520px;
    background: var(--white);
  }
  .back-name {
    position: absolute; top: 26px; right: 44px;
    font-size: 25px; font-weight: 800; letter-spacing: 0.3px; line-height: 1.2;
  }
  .back-name .first { color: var(--orange); }
  .back-name .last { color: var(--blue); }
  .name-marker {
    position: absolute; top: 28px; right: 0; width: 28px; height: 26px; background: var(--orange);
  }
  .back-brand { position: absolute; left: 28px; top: 92px; }
  .back-brand .brand-row { display: flex; align-items: center; gap: 10px; }
  .back-brand .brand-square { width: 22px; height: 22px; background: var(--orange); }
  .back-brand .brand-name {
    font-size: 44px; font-weight: 800; color: var(--blue); letter-spacing: -1px; line-height: 1;
  }
  .back-brand .tagline {
    margin-top: 4px; margin-left: 32px; font-size: 17px; color: var(--blue); letter-spacing: -0.3px;
  }
  .contact-band {
    position: absolute; left: 0; bottom: 0; width: 100%; height: 128px; background: var(--orange);
  }
  .side-panel {
    position: absolute; right: 0; top: 150px; width: 150px; height: 170px;
    background: var(--blue);
  }
  .side-panel .panel-square {
    position: absolute; left: 40px; top: 42px; width: 70px; height: 70px; background: var(--white);
  }
  .contact {
    position: absolute; left: 28px; bottom: 14px; color: var(--white);
    font-size: 14px; line-height: 1.32;
  }
  .contact .services { margin-bottom: 6px; }
  .contact-line { display: flex; align-items: center; gap: 8px; }
  .contact-line svg { width: 13px; height: 13px; flex: none; }
</style>
</head>
<body>
  <section class="card card-front" aria-label="Card front">
    <div class="front-brand">
      <span class="brand-square"></span>
      <span class="brand-name">Vextorial</span>
    </div>
    <p class="front-tagline">developer of custom applications</p>
  </section>

  <section class="card card-back" aria-label="Card back">
    <p class="back-name"><span class="first">Dale</span> <span class="last">Parker</span></p>
    <span class="name-marker"></span>

    <div class="back-brand">
      <div class="brand-row">
        <span class="brand-square"></span>
        <span class="brand-name">Vextorial</span>
      </div>
      <p class="tagline">developer of custom applications</p>
    </div>

    <div class="contact-band"></div>
    <div class="side-panel"><span class="panel-square"></span></div>

    <div class="contact">
      <p class="services">Bitcoin education &amp; custody for business<br>Bitcoin payments for your existing systems</p>
      <p class="contact-line">
        <svg viewBox="0 0 16 16" aria-hidden="true"><path fill="#fff" d="M3 1h3l1.5 4-2 1.2a9 9 0 0 0 4.3 4.3L11 8.5l4 1.5v3a2 2 0 0 1-2 2A12 12 0 0 1 1 3a2 2 0 0 1 2-2z"/></svg>
        (888) 555-VXTRL
      </p>
      <p class="contact-line">
        <svg viewBox="0 0 16 16" aria-hidden="true"><circle cx="8" cy="8" r="6.5" fill="none" stroke="#fff" stroke-width="1.5"/><path d="M1.5 8h13M8 1.5c-3 3.5-3 9.5 0 13M8 1.5c3 3.5 3 9.5 0 13" fill="none" stroke="#fff" stroke-width="1.2"/></svg>
        www.vextorial.com
      </p>
      <p class="contact-line">
        <svg viewBox="0 0 16 16" aria-hidden="true"><rect x="1" y="3" width="14" height="10" fill="none" stroke="#fff" stroke-width="1.5"/><path d="M1 3l7 6 7-6" fill="none" stroke="#fff" stroke-width="1.5"/></svg>
        dale@vextorial.com
      </p>
    </div>
  </section>
</body>
</html>
```